Redesign of an existing homepage

This site needs a redesign
https://www.wanderhof-kelbach.de
This page with the accommodation options is important for the customer
https://www.wanderhof-kelbach.de/gastgeber/
Till now there is a new logo. See attachment. That's all I have.
It would make sense to use the colors of the logo in the redesign.
footer.jpg.
I would put this info into the footer. The graphic (Infomaterial) is not needed.
a new menu - links.jpg
This info can be put in a new menu. Therefore the right column is gone and there is more space for the design.
NEW:
Please keep in mind that the Icons are important and shall be displayed under every accommodation

```html
<!DOCTYPE html>
<html lang="en">
<head>
<meta charset="utf-8">
<title>Fremdenverkehrsverein Kelbach – Holidays in the Kelbachtal</title>
<link href="https://fonts.googleapis.com/css2?family=Montserrat:wght@400;500;600;700&display=swap" rel="stylesheet">
<style>
:root{
  --blue:#2a8fd6;
  --navy:#1d3f8f;
  --green:#5aa62a;
  --ink:#1a1a1a;
  --text:#444;
  --muted:#777;
  --footer:#161616;
  --white:#fff;
}
*{box-sizing:border-box;margin:0;padding:0}
html,body{width:1200px;height:4292px;overflow:hidden}
body{font-family:'Montserrat',sans-serif;color:var(--text);background:var(--white);position:relative}
.abs{position:absolute}

/* header */
.site-header{position:absolute;left:0;top:0;width:1200px;height:128px;background:var(--white)}
.brand-panel{position:absolute;left:0;top:0;width:275px;height:128px;border-right:4px solid var(--green);border-bottom-right-radius:120px 128px;background:var(--white);z-index:2}
.brand-dot{position:absolute;left:98px;top:6px;width:72px;height:72px;border-radius:50%;background:var(--green)}
.brand-name{position:absolute;left:40px;top:84px;font-weight:700;font-size:17px;color:var(--navy);line-height:1.1}
.brand-name small{display:block;font-weight:500;font-size:17px;color:var(--ink)}
.partners{position:absolute;left:320px;top:6px;display:flex;gap:40px;align-items:center}
.badge{height:64px;background:#e4eef7;border-radius:6px}
.badge.round{width:64px;border-radius:50%;background:#cfe3b8}
.badge.w1{width:170px}
.badge.sq{width:86px;background:#cfd9ea}
.badge.w2{width:160px;background:#e6e6e6}
.phone{position:absolute;left:926px;top:20px;display:flex;align-items:center;gap:14px;font-size:14px;color:var(--ink)}
.phone-ico{width:36px;height:36px;border-radius:50%;background:var(--blue);display:flex;align-items:center;justify-content:center}
.main-nav{position:absolute;left:275px;top:77px;width:925px;height:51px;background:var(--blue);display:flex;align-items:center;padding-left:60px;gap:0}
.main-nav a{color:var(--white);text-decoration:none;font-size:14px;padding:0 19px;height:51px;line-height:51px}
.main-nav a.active{background:var(--green);font-weight:700}

/* hero */
.hero{position:absolute;left:0;top:128px;width:1200px;height:557px;background:linear-gradient(180deg,#6c7f8f 0%,#a48b6a 40%,#4d4a34 75%,#2c3a22 100%)}
.hero h1{position:absolute;top:148px;width:100%;text-align:center;color:var(--white);font-weight:700;font-size:50px;line-height:60px;text-shadow:0 2px 6px rgba(0,0,0,.4)}
.hero h1 span{font-size:38px}
.btn{display:inline-block;color:var(--white);font-weight:700;font-size:15px;border-radius:8px;text-decoration:none;text-align:center}
.hero .btn{position:absolute;left:512px;top:292px;width:175px;height:46px;line-height:46px;background:var(--green)}
.dots{position:absolute;display:flex;gap:10px}
.dots i{width:15px;height:15px;border-radius:50%;border:2px solid var(--green)}
.dots i.on{background:var(--green)}
.hero .dots{left:565px;top:500px}
.hero .dots i{border-color:var(--green)}

/* welcome */
.welcome{position:absolute;top:685px;left:0;width:1200px;text-align:center}
.welcome .mark{width:72px;height:72px;border-radius:50%;background:var(--green);margin:76px auto 0}
.welcome h2{font-size:37px;font-weight:600;color:var(--ink);margin-top:22px}
.welcome p.body{font-size:14px;line-height:28.3px;color:var(--text);width:860px;margin:22px auto 0}
.welcome .tagline{font-size:22px;color:var(--blue);font-weight:500;margin-top:24px}
.welcome .sign{font-size:14px;line-height:28px;margin-top:24px}

/* hosts */
.section-title{position:absolute;left:111px;font-size:37px;font-weight:600;color:var(--ink)}
.arrows{position:absolute;left:995px;top:1392px;display:flex;gap:14px}
.arrows span{width:40px;height:40px;border-radius:50%;border:3px solid #bbb;display:flex;align-items:center;justify-content:center}
.arrows span.next{border-color:var(--navy)}
.host-card{position:absolute;top:1468px;width:286px;height:339px;overflow:hidden}
.host-card .ph{position:absolute;inset:0}
.host-card .cap{position:absolute;left:26px;bottom:30px;right:20px;color:var(--white);font-weight:500;font-size:19px;line-height:30px}
.host-card .cap::after{content:"";display:block;width:80px;height:5px;background:var(--green);margin-top:14px}
.host-card.feature .ph{background:linear-gradient(180deg,#b9c5cf,#6a7280)}
.host-card.feature .shade{position:absolute;inset:0;background:rgba(20,35,80,.45)}
.host-card.feature .cap{bottom:auto;top:180px}
.host-card.feature .cap::after{background:var(--white)}
.host-card.feature p{position:absolute;left:24px;top:240px;right:30px;color:var(--white);font-size:14px;line-height:28px}

/* video */
.video{position:absolute;top:1913px;left:0;width:1200px;height:477px;background:linear-gradient(135deg,#5a6a3a,#8a4a3a 45%,#6c6c5c 70%,#3e5530)}
.video .mark{position:absolute;left:564px;top:88px;width:72px;height:72px;border-radius:50%;background:var(--green)}
.video h2{position:absolute;top:170px;width:100%;text-align:center;color:var(--white);font-size:40px;font-weight:600}
.play{position:absolute;left:553px;top:244px;width:94px;height:94px;border-radius:50%;background:rgba(255,255,255,.25);display:flex;align-items:center;justify-content:center}
.play span{width:72px;height:72px;border-radius:50%;background:var(--green);display:flex;align-items:center;justify-content:center}

/* property */
.prop-photo{position:absolute;top:2547px;height:486px}
.prop-card{position:absolute;top:2953px;height:307px;background:var(--white);border-radius:8px;box-shadow:0 4px 20px rgba(0,0,0,.15);padding:28px 42px;overflow:hidden}
.prop-card h3{font-size:26px;font-weight:600;color:var(--navy)}
.prop-card .addr{margin-top:12px;display:flex;gap:14px;font-size:19px;font-weight:500;color:var(--ink);line-height:30px}
.prop-card p{font-size:14px;line-height:28px;margin-top:8px;color:var(--text)}
.prop-card .btn{position:absolute;left:57px;bottom:30px;width:174px;height:46px;line-height:46px;background:var(--green)}
.amenity{position:absolute;right:20px;bottom:28px;width:56px;height:48px;border:2px solid var(--ink);border-radius:6px;display:flex;align-items:center;justify-content:center}

/* book band */
.book{position:absolute;top:3270px;left:0;width:1200px;height:478px;background:linear-gradient(180deg,#ffffff 0%,#cfd3cf 18%,#7b8068 55%,#4b5a2e 100%)}
.book h2{position:absolute;top:210px;width:100%;text-align:center;color:var(--white);font-size:37px;font-weight:600;line-height:56px}
.book .btn{position:absolute;left:512px;top:333px;width:175px;height:46px;line-height:46px;background:var(--blue)}

/* footer */
.site-footer{position:absolute;top:3747px;left:0;width:1200px;height:545px;background:var(--footer);color:var(--white)}
.f-brand{position:absolute;left:100px;top:78px;width:245px;text-align:center}
.f-brand .mark{width:90px;height:90px;border-radius:50%;background:var(--green);margin:0 auto}
.f-brand .name{font-size:20px;font-weight:700;color:var(--blue);margin-top:14px;line-height:1.2}
.f-brand h4{font-size:19px;font-weight:600;margin-top:14px}
.f-brand a{color:var(--white);font-size:14px;line-height:30px;display:block;margin-top:8px}
.f-col{position:absolute;top:80px}
.f-col h4{font-size:20px;font-weight:600;margin-bottom:26px}
.f-col li{list-style:none;font-size:14px;line-height:30px}
.contact li{display:flex;gap:10px}
.contact b{font-weight:600}
.contact .ic{width:14px;flex:none;padding-top:7px}
.f-rule{position:absolute;left:100px;top:475px;width:978px;height:1px;background:#555}
.copy{position:absolute;top:492px;width:100%;text-align:center;font-size:14px}
</style>
</head>
<body>

<header class="site-header">
  <div class="brand-panel">
    <div class="brand-dot"></div>
    <div class="brand-name">FREMDENVERKEHRSVEREIN<small>KELBACH</small></div>
  </div>
  <div class="partners">
    <div class="badge round"></div>
    <div class="badge w1"></div>
    <div class="badge sq"></div>
    <div class="badge w2"></div>
  </div>
  <div class="phone">
    <span class="phone-ico"><svg width="18" height="18" viewBox="0 0 24 24"><path fill="#fff" d="M6.6 10.8a15 15 0 0 0 6.6 6.6l2.2-2.2c.3-.3.7-.4 1-.2 1.1.4 2.3.6 3.6.6.6 0 1 .4 1 1V20c0 .6-.4 1-1 1A17 17 0 0 1 3 4c0-.6.4-1 1-1h3.5c.6 0 1 .4 1 1 0 1.3.2 2.5.6 3.6.1.3 0 .7-.2 1z"/></svg></span>
    08571 / 482 3310
  </div>
  <nav class="main-nav">
    <a class="active" href="https://www.wanderhof-kelbach.de">HOME</a>
    <a href="https://www.wanderhof-kelbach.de/gastgeber/">HOST</a>
    <a href="#">KELBACHTAL</a>
    <a href="#">LEISURE</a>
    <a href="#">DESTINATIONS</a>
    <a href="#">ART AND CULTURE</a>
    <a href="#">CONTACT</a>
  </nav>
</header>

<section class="hero" role="img" aria-label="Mediterranean style villa with palm trees at sunset">
  <h1>HOLIDAYS IN THE KELBACHTAL -<br><span>THE MOST BEAUTIFUL SPOT IN BAVARIA</span></h1>
  <a class="btn" href="#">EXPLORE NOW</a>
  <div class="dots"><i class="on"></i><i></i><i></i></div>
</section>

<section class="welcome">
  <div class="mark"></div>
  <h2>DEAR VISITORS,</h2>
  <p class="body">Parish churches and the surrounding area have everything that makes life worth living:<br>
  culture and nature, joie de vivre and enjoyment, friendly and open-minded people...<br>
  Whether churches, fountains or other architectural monuments - on a tour of the Kelbacher Ross town you can discover many loving details for yourself.<br>
  For those who like to exercise and seek relaxation, there is "pure nature" in and around Kelbach! Here you can be sporty while cycling, walking, hiking, golfing, riding and swimming or simply enjoy the peace and quiet.<br>
  Leisure and relaxation for the whole family – plan a holiday on the farm, in a holiday apartment or in a hotel. Your holiday in the Kelbachtal will be a unique experience!<br>
  Enjoy our hospitality – a visit is worthwhile at any time of the year.</p>
  <p class="tagline">We look forward to seeing you!</p>
  <p class="sign">You<br>Tourist Office Kelbach and Surroundings</p>
</section>

<h2 class="section-title" style="top:1386px">HOSTS IN THE KELBACHTAL</h2>
<div class="arrows">
  <span><svg width="14" height="18" viewBox="0 0 14 18"><path d="M10 2 3 9l7 7" stroke="#bbb" stroke-width="2.5" fill="none"/></svg></span>
  <span class="next"><svg width="14" height="18" viewBox="0 0 14 18"><path d="m4 2 7 7-7 7" stroke="#1d3f8f" stroke-width="2.5" fill="none"/></svg></span>
</div>

<a class="host-card feature" style="left:112px" href="https://www.wanderhof-kelbach.de/gastgeber/">
  <div class="ph" role="img" aria-label="Farmhouse courtyard with white building"></div>
  <div class="shade"></div>
  <div class="cap">Farm holidays</div>
  <p>The Lindenhof is located on the side of the district town of Kelbach on a small ridge.</p>
</a>
<div class="host-card" style="left:428px">
  <div class="ph" role="img" aria-label="Cows grazing on a meadow" style="background:linear-gradient(180deg,#dfe3e0,#7d8a5e 70%,#3e5028)"></div>
  <div class="cap">Bio-Ferienhof<br>Lindner</div>
</div>
<div class="host-card" style="left:745px">
  <div class="ph" role="img" aria-label="Aerial view of a lakeside hotel" style="background:linear-gradient(160deg,#4d6b3a,#8a5a45 50%,#3a5a30)"></div>
  <div class="cap">Seehotel Brunnwies<br>(Dog Hotel)</div>
</div>
<div class="host-card" style="left:1062px">
  <div class="ph" role="img" aria-label="Hotel room with curtains" style="background:linear-gradient(90deg,#a8906a,#e9e7e0 60%,#cfcac0)"></div>
  <div class="cap">Parkhotel<br>Kelbach</div>
</div>

<section class="video" role="img" aria-label="Aerial view of the town with red roofs">
  <div class="mark"></div>
  <h2>WATCH THE VIDEO</h2>
  <div class="play"><span><svg width="26" height="30" viewBox="0 0 26 30"><path d="M4 2l20 13L4 28z" fill="#fff"/></svg></span></div>
</section>

<h2 class="section-title" style="top:2470px">OUR PROPERTY</h2>

<section class="book" role="img" aria-label="Village with church tower and green fields">
  <h2>EVERY GREAT TRIP BEGINS WITH A<br>GREAT BOOK</h2>
  <a class="btn" href="#">BOOK NOW</a>
</section>

<div class="prop-photo" style="left:112px;width:873px;background:linear-gradient(180deg,#7fa2c8,#5a4b34 45%,#3e5a2a)" role="img" aria-label="Traditional Bavarian wooden farmhouse with balcony"></div>
<div class="prop-photo" style="left:1018px;width:200px;background:linear-gradient(180deg,#6d95cf,#c8d4e4 55%,#6d4a30)" role="img" aria-label="Holiday house under blue sky"></div>

<article class="prop-card" style="left:145px;width:810px">
  <h3>Webergütl</h3>
  <div class="addr">
    <svg width="18" height="26" viewBox="0 0 18 26" style="margin-top:4px"><path d="M9 1a8 8 0 0 0-8 8c0 6 8 16 8 16s8-10 8-16a8 8 0 0 0-8-8z" fill="#2a8fd6"/><circle cx="9" cy="9" r="3.2" fill="#fff"/></svg>
    <div>Au 3, 84390 Kelbach-Au<br>1 residential unit</div>
  </div>
  <p>With us you can expect an unforgettable, relaxing and quiet holiday for the whole family. Our country house is idyllically located between forest and meadows. Close to a wonderful local recreation area Kelbachsee Oberau.</p>
  <a class="btn" href="#">READ MORE</a>
  <span class="amenity"><svg width="30" height="30" viewBox="0 0 30 30" fill="none" stroke="#1a1a1a" stroke-width="2"><circle cx="11" cy="6" r="3"/><path d="M11 10v10l-5 7M11 20l6 7M6 15h10l6-6"/></svg></span>
</article>
<article class="prop-card" style="left:1050px;width:300px">
  <h3>Ferien am Lindenhof</h3>
  <div class="addr">
    <svg width="18" height="26" viewBox="0 0 18 26" style="margin-top:4px"><path d="M9 1a8 8 0 0 0-8 8c0 6 8 16 8 16s8-10 8-16a8 8 0 0 0-8-8z" fill="#2a8fd6"/><circle cx="9" cy="9" r="3.2" fill="#fff"/></svg>
    <div>Linden 1, Kelbach<br>8 accommodations</div>
  </div>
  <p>The Lindenhof offers a wonderful view afar. Guests love it.</p>
  <a class="btn" href="#" style="left:58px">READ MORE</a>
</article>

<div class="dots" style="left:565px;top:3304px"><i class="on"></i><i></i><i></i></div>

<footer class="site-footer">
  <div class="f-brand">
    <div class="mark"></div>
    <div class="name">FREMDENVERKEHRSVEREIN<br><span style="color:#fff;font-weight:500">KELBACH</span></div>
    <h4>Information material</h4>
    <a href="#">Request information material»</a>
  </div>
  <div class="f-col" style="left:406px">
    <h4>Main Links</h4>
    <ul><li>Home</li><li>Host</li><li>Kelbachtal</li><li>Leisure</li><li>Destinations</li><li>Art and culture</li><li>Contact</li></ul>
  </div>
  <div class="f-col" style="left:611px">
    <h4>Opening hours:</h4>
    <ul><li>Mon-Fri 9:00 a.m. – 5:00 p.m.</li><li>May-October:</li><li>Sat 9:00 a.m. – 12:00 p.m.</li></ul>
  </div>
  <div class="f-col contact" style="left:860px">
    <h4>Contact Details</h4>
    <ul>
      <li><span class="ic"><svg width="12" height="14" viewBox="0 0 24 24"><path fill="#fff" d="M6.6 10.8a15 15 0 0 0 6.6 6.6l2.2-2.2c.3-.3.7-.4 1-.2 1.1.4 2.3.6 3.6.6.6 0 1 .4 1 1V20c0 .6-.4 1-1 1A17 17 0 0 1 3 4c0-.6.4-1 1-1h3.5c.6 0 1 .4 1 1 0 1.3.2 2.5.6 3.6.1.3 0 .7-.2 1z"/></svg></span><div><b>Call Us</b><br>08571 / 482 3310</div></li>
      <li><span class="ic"><svg width="14" height="14" viewBox="0 0 14 14"><rect x="1" y="5" width="12" height="8" fill="#fff"/><rect x="3" y="1" width="8" height="4" fill="none" stroke="#fff"/></svg></span><div><b>Fax</b><br>08571 / 482 3319</div></li>
      <li><span class="ic"><svg width="14" height="11" viewBox="0 0 14 11"><rect x="0.5" y="0.5" width="13" height="10" fill="#fff"/><path d="M1 1l6 5 6-5" stroke="#161616" fill="none"/></svg></span><div><b>Mail Us</b><br>info@wanderhof-kelbach.de</div></li>
      <li><span class="ic"><svg width="13" height="18" viewBox="0 0 18 26"><path d="M9 1a8 8 0 0 0-8 8c0 6 8 16 8 16s8-10 8-16a8 8 0 0 0-8-8z" fill="#fff"/><circle cx="9" cy="9" r="3.2" fill="#161616"/></svg></span><div><b>Location</b><br>Fremdenverkehrsverein Kelbach<br>und Umgebung e. V.<br>Marktplatz 4<br>84399 Kelbach</div></li>
    </ul>
  </div>
  <div class="f-rule"></div>
  <p class="copy">© 2025 Fremdenverkehrsverein Kelbach I All Rights Reserved</p>
</footer>

</body>
</html>
```